Buch-/eBook-Cover für Sachbuch gesucht
Zielgruppe
We're selfpublishing nonfiction books. Interested are adults - mostly man (age range: 25-50) - who want to learn more about leadership at their workplaces.
Aufgabenstellung
The design should be clean and simple, title easy to read, good color contrast (the cover has to stand out from an white background).

```html
<!DOCTYPE html>
<html lang="en">
<head>
<meta charset="utf-8">
<title>Leadership – Book Cover</title>
<link rel="stylesheet" href="https://fonts.googleapis.com/css2?family=Barlow+Semi+Condensed:wght@700&family=Barlow:ital,wght@1,400&family=Source+Sans+3:wght@400&display=swap">
<style>
  :root {
    --page: #ffffff;
    --ink-dark: #050607;
    --ink-deep: #0b1420;
    --swirl-blue: #1d3f78;
    --gold-light: #f3d03a;
    --gold: #e0b022;
    --gold-deep: #b88a12;
    --author-grey: #9a9a9a;
    --subtitle: #ffffff;
  }
  html, body {
    margin: 0;
    padding: 0;
    width: 884px;
    height: 1200px;
    overflow: hidden;
    background: var(--page);
  }
  .canvas {
    position: relative;
    width: 884px;
    height: 1200px;
    background: var(--page);
  }
  .cover {
    position: absolute;
    left: 75px;
    top: 54px;
    width: 724px;
    height: 1087px;
    background: var(--ink-dark);
    overflow: hidden;
  }
  .cover-texture {
    position: absolute;
    inset: 0;
    background:
      radial-gradient(ellipse 60% 14% at 30% 38%, rgba(29,63,120,0.55), transparent 70%),
      radial-gradient(ellipse 70% 16% at 55% 52%, rgba(29,63,120,0.45), transparent 70%),
      radial-gradient(ellipse 50% 12% at 20% 62%, rgba(29,63,120,0.35), transparent 70%),
      radial-gradient(ellipse 60% 20% at 70% 20%, rgba(11,20,32,0.9), transparent 70%),
      linear-gradient(180deg, var(--ink-dark) 0%, var(--ink-deep) 45%, var(--ink-dark) 100%);
  }
  .cover-art {
    position: absolute;
    inset: 0;
  }
  .title {
    font-family: "Barlow Semi Condensed", "Arial Narrow", sans-serif;
    font-weight: 700;
    font-size: 140px;
    fill: url(#gold-foil);
  }
  .arrow-shaft { stroke: url(#gold-foil); stroke-width: 5; }
  .arrow-head { fill: var(--gold); }
  .author {
    font-family: "Source Sans 3", "Myriad Pro", sans-serif;
    font-size: 28px;
    fill: var(--author-grey);
  }
  .subtitle-rule { stroke: var(--gold); stroke-width: 3; }
  .subtitle-line {
    font-family: "Barlow", "Arial", sans-serif;
    font-style: italic;
    font-weight: 400;
    font-size: 46px;
    fill: var(--subtitle);
  }
</style>
</head>
<body>
<main class="canvas">
  <section class="cover">
    <div class="cover-texture" role="img" aria-label="Dark fluid marble texture with deep blue swirls"></div>
    <svg class="cover-art" width="724" height="1087" viewBox="0 0 724 1087" xmlns="http://www.w3.org/2000/svg">
      <defs>
        <linearGradient id="gold-foil" x1="0" y1="0" x2="1" y2="1">
          <stop offset="0" stop-color="#f3d03a"/>
          <stop offset="0.5" stop-color="#e0b022"/>
          <stop offset="1" stop-color="#c99a18"/>
        </linearGradient>
      </defs>

      <text class="title" transform="translate(203,994) rotate(-90)" textLength="884" lengthAdjust="spacingAndGlyphs">LEADERSHIP</text>

      <g class="growth-arrow">
        <line class="arrow-shaft" x1="274" y1="90" x2="274" y2="994"/>
        <polygon class="arrow-head" points="274,56 261,96 287,96"/>
      </g>

      <text class="author" x="318" y="241">Daniel Hargrove</text>

      <g class="subtitle" transform="translate(318,609) rotate(-6)">
        <line class="subtitle-rule" x1="0" y1="0" x2="262" y2="0"/>
        <line class="subtitle-rule" x1="0" y1="64" x2="262" y2="64"/>
        <line class="subtitle-rule" x1="0" y1="128" x2="262" y2="128"/>
        <line class="subtitle-rule" x1="0" y1="192" x2="262" y2="192"/>
        <line class="subtitle-rule" x1="0" y1="256" x2="262" y2="256"/>
        <text class="subtitle-line" x="8" y="50">Fostering</text>
        <text class="subtitle-line" x="8" y="114">Growth and</text>
        <text class="subtitle-line" x="8" y="178">Inspiring</text>
        <text class="subtitle-line" x="8" y="242">Excellence</text>
      </g>
    </svg>
  </section>
</main>
</body>
</html>
```